Blue Heron Journeys

We are a predominantly online travel agency with high-end (first/business class) clients. I'm looking to either have our existing logo revamped or a new logo created with business card layout. I prefer to work with existing logo if possible so it remains familiar with existing clientele. I have uploaded a yellow business card layout showing icons on one side of the card. I would like to keep my existing colours, not yellow. could the company name/tag line go over the icons?
Industry/Entity Type
Business
Contact Information for Business Card
Lucinda Fairley
Director
(I.A.T.A. 07715463)
(Corvano Pty. Ltd) ABN 61 574 203 918
512/18 Kendrick Lane
Wattle Reach | NSW 2577 | Australia
www.blueheronjourneys.com.au
m: + 61 (0) 417 588 130
t: + 61 (0) 2 9416 2058
e: lucinda@blueheronjourneys.com.au

```html
<!DOCTYPE html>
<html lang="en">
<head>
<meta charset="utf-8">
<title>Blue Heron Journeys – Business Card</title>
<link href="https://fonts.googleapis.com/css2?family=Roboto:ital,wght@0,300;0,400;0,500;0,700;1,400&family=Roboto+Condensed:wght@400;700&display=swap" rel="stylesheet">
<style>
  :root {
    --backdrop: #e2e2e2;
    --paper: #fdfdfc;
    --band: #e3eaf0;
    --ink: #111418;
    --text-grey: #4b5157;
    --back-card: #131417;
    --back-logo: #e9e9ec;
    --back-url: #c9d6e2;
  }
  * { margin: 0; padding: 0; box-sizing: border-box; }
  html, body {
    width: 1200px; height: 960px; overflow: hidden;
    background: var(--backdrop);
    font-family: "Roboto", Arial, sans-serif;
  }
  .card {
    position: absolute;
    width: 600px; height: 342px;
    border-radius: 20px;
    overflow: hidden;
  }
  .card--front { left: 314px; top: 114px; background: var(--paper); }
  .card--back  { left: 311px; top: 472px; background: var(--back-card); }

  .front-split { position: absolute; inset: 0; }

  .brand-name {
    position: absolute;
    left: 342px; top: 80px; width: 230px;
    text-align: center;
    font-size: 21px; font-weight: 400;
    color: var(--ink);
  }

  .address {
    position: absolute; left: 29px; top: 173px;
    font-size: 14px; line-height: 18px;
    color: var(--text-grey);
  }
  .contact-list {
    position: absolute; left: 29px; top: 222px;
    list-style: none;
  }
  .contact-list li {
    display: flex; align-items: center;
    height: 19.4px;
    font-size: 14px; color: var(--text-grey);
  }
  .contact-list svg { width: 14px; height: 14px; margin-right: 9px; fill: var(--ink); flex: none; }

  .person {
    position: absolute; right: 48px; top: 252px;
    text-align: right;
  }
  .person__name {
    font-family: "Roboto Condensed", "Arial Narrow", sans-serif;
    font-weight: 700; font-size: 21px; color: var(--ink);
    line-height: 26px;
  }
  .person__title {
    font-family: "Roboto Condensed", "Arial Narrow", sans-serif;
    font-weight: 700; font-size: 15px; color: var(--text-grey);
    line-height: 20px;
  }
  .person__reg {
    font-size: 11px; line-height: 15px; color: var(--text-grey);
  }
  .person__reg:first-of-type { margin-top: 4px; }

  .back-brand {
    position: absolute; left: 0; right: 0; top: 152px;
    text-align: center;
    font-size: 26px; font-weight: 300;
    color: var(--back-logo);
  }
  .back-url {
    position: absolute; left: 0; right: 0; top: 262px;
    text-align: center;
    font-size: 14px; font-style: italic; letter-spacing: 1.4px;
    color: var(--back-url);
  }
</style>
</head>
<body>
  <section class="card card--front" aria-label="Business card front">
    <svg class="front-split" width="600" height="342" viewBox="0 0 600 342" aria-hidden="true">
      <polygon points="0,114 600,250 600,342 0,342" fill="var(--band)"/>
      <line x1="0" y1="114" x2="600" y2="250" stroke="var(--ink)" stroke-width="4"/>
    </svg>

    <div class="brand-name">Blue Heron Journeys</div>

    <p class="address">512/18 Kendrick Lane<br>Wattle Reach | NSW 2577 | Australia</p>

    <ul class="contact-list">
      <li><svg viewBox="0 0 24 24"><path d="M7 1h10a2 2 0 0 1 2 2v18a2 2 0 0 1-2 2H7a2 2 0 0 1-2-2V3a2 2 0 0 1 2-2zm0 3v14h10V4zm5 15.5a1 1 0 1 0 0 2 1 1 0 0 0 0-2z"/></svg>+ 61 (0) 417 588 130</li>
      <li><svg viewBox="0 0 24 24"><path d="M6.6 10.8a15 15 0 0 0 6.6 6.6l2.2-2.2c.3-.3.7-.4 1-.2 1.1.4 2.3.6 3.6.6.6 0 1 .4 1 1V20c0 .6-.4 1-1 1A17 17 0 0 1 3 4c0-.6.4-1 1-1h3.5c.6 0 1 .4 1 1 0 1.3.2 2.5.6 3.6.1.3 0 .7-.2 1z"/></svg>+ 61 (0) 2 9416 2058</li>
      <li><svg viewBox="0 0 24 24"><path d="M2 5h20v14H2zm2 2v.5l8 5 8-5V7l-8 5z"/></svg>lucinda@blueheronjourneys.com.au</li>
      <li><svg viewBox="0 0 24 24"><circle cx="12" cy="12" r="10"/><path d="M12 2c-3 3-3 17 0 20M2 12h20" stroke="var(--band)" stroke-width="1.6" fill="none"/></svg>www.blueheronjourneys.com.au</li>
    </ul>

    <div class="person">
      <div class="person__name">LUCINDA FAIRLEY</div>
      <div class="person__title">DIRECTOR</div>
      <p class="person__reg">I.A.T.A. 07715463</p>
      <p class="person__reg">Corvano Pty. Ltd ABN 61 574 203 918</p>
    </div>
  </section>

  <section class="card card--back" aria-label="Business card back">
    <div class="back-brand">Blue Heron Journeys</div>
    <div class="back-url">www.blueheronjourneys.com.au</div>
  </section>
</body>
</html>
```